Corporate website design needed

We need a Contemporary Industrial/Tech/Logistics Website design to match our logistic client's business. Our client consults and build logistics solutions that they manage but they are not a typical 3PL (3rd party logistics company) which is primarily engaged in moving boxes.
PSD file only for now, home and default templates.
COMPANY CHARACTER
DESIGN LOOK AND FEEL
• The design should also be modern and visually well organized — employing a combination of visual devices and info graphics. Keep it light and not too heavy but strong/ professional. And unique.
• The design should go beyond the typical industrial pick and pack 3PL representing [Logistics Company] as a High Tech/IT logistics company.
Some examples although these are not right for this client because they have much more content and present themselves more as a 3pl.
http://www.vobrelink-hub.example/ (More right then wrong - Like this but simplified)
http://www.durmaxfreight.example (Ugly)
http://www.tpwallerton.example (More right then wrong but different focus)
http://www.pelhamrye.example/ Too 3PL trucking… We want a bit ore high level approach
The difference, the design should be a fusion in core concepts that culminate in a design which implies the following attributes. Tech (Big data / analytics / software), Consultancy (Solutions, SME, Leader), 3PL Industry vertical solutions.
NOTE: The visualization of “tech” is not “1” and “0”, but more “software and analytics” Perhaps more like www.navimetra.example.
• They need to be seen as a solutions provider in Logistics and as in Subject matter experts
TONE
The tone needs to exude professionalism, expertise, though leadership along with technical and executional excellence.
Experienced
Knowledgeable
Confident
Determined
Straightforward
WEBSITE OBJECTIVES
• Focus C-Suite executives and logistics managers’ attention on [Logistics Company]s commanding knowledge and expertise, and unique approach to supply chain solutions producing more RFP wins
• Create an easy to scan design which decreases the reliance on text through featured text, summaries, and smaller “chunked” size bits of information.
• Convey [Logistics Company] as high-tech 3PL solutions developer and services provider with a ‘high-touch’ consultative approach.
• Showcase [Logistics Company]’s value propositions. (See Slider Content)
• Showcase [Logistics Company]’s expertise in logistical analytics.
• Gain recognition as an industry leader in evolutionary new space (supply chain 2.0)
WEBSITE STRATEGY
• Reduce reliance on text (at least within initial entry points for each section)
• Typography: Watch text line lengths and readability, bolder fonts. NO SERIFS
• Generally, create a click-through format so that users who want more details can find it, and those who don’t can get a snapshot without clicking through.
• Increase visual content through info graphics and some dynamic content, photography
• Better utilize the space on each page (e.g., add visual interest, photography and iconography where appropriate to break up copy blocks and maintain readable line lengths).
COLOR SCHEME
• Create a more engaging color scheme (the logo will remain the same under all circumstances).
• Red / grayscale may work…. Not too dark or heavy. Not too much red. Ex. quiltora.example
• Also try blues and greys. They seem to like that. Open to suggestions but don’t get to crazy. Red is in their logo but too much may be a problem.
PHOTOGRAPHY
Yes. And I will upload some.
If you pick photography please be sure to note Which stock house used and the image number!
CONTENT
The content will be presented in a more hierarchical format — with lead-ins, paragraph and section headers and navigational cues to expand lengthier content allowing the visitor to more easily scan the website. No case studies, No Social media, News while on the home page should not be over emphasized. They don't post a lot so it gets dated quickly ...
I will be uploading a wire frame and other elements.
NOTE: I uploaded my EXAMPLE mock up which is close but not close enough.
I am not a great designer. So I am looking for an alternative that exceed my design ability! These examples show the basic layout but I really want some varied alternatives.
The colors are inconsistent and type not quite right. The grey bar at top is not right and should probably go away.
Please pull the basic elements in the example together into a great design.
If you have questions please contact me.
i will upload some photography tomorrow that may be of use.
Thanks!
Updates
Hi All,
We are still evaluating the submitted designs. Sorry for the delay.
Target Market(s)
This website is primarily a validation website. Few new customers will search and find them as such...
The site should be Focused on C-Suite executives and logistics managers’ attention on [Logistics Company]s commanding knowledge and expertise, and unique approach to supply chain solutions producing more RFP wins
Industry/Entity Type
Business
Font styles to use
Requirements
Must have
- Slide show, Clearly explain who they are and what they do.
Create an easy to scan design which decreases the reliance on text through featured text, summaries, and smaller “chunked” size bits of information.
Convey [Logistics Company] as high-tech 3PL solutions developer and services
provider with a ‘high-touch’ consultative approach.
Should not have
- No Ads space
No Social media
Not too cluttered. Keep it clean.

```html
<!DOCTYPE html>
<html lang="en">
<head>
<meta charset="utf-8">
<title>Veltrane Logistics</title>
<link rel="stylesheet" href="https://fonts.googleapis.com/css2?family=Open+Sans:ital,wght@0,300;0,400;0,600;0,700;1,400&family=Montserrat:wght@400;500&family=Arimo:ital,wght@0,400;1,400&display=swap">
<style>
:root{
  --blue:#1a7fc1;
  --blue-deep:#0f5d96;
  --cyan:#2fb1f0;
  --red:#d9141c;
  --ink:#333;
  --muted:#6f6f6f;
  --soft:#9a9a9a;
  --rule:#d9d9d9;
  --panel:#f5f5f5;
  --footer:#2f2f2f;
  --footer-base:#232323;
  --footer-text:#b9b9b9;
  --white:#fff;
}
*{box-sizing:border-box;margin:0;padding:0}
html,body{width:703px;height:1200px;overflow:hidden;background:var(--white)}
body{position:relative;font-family:"Open Sans",Arial,sans-serif;color:var(--ink)}
h1,h2,h3{font-weight:400}
.abs{position:absolute}
a{color:inherit;text-decoration:none}

/* header */
.brand{left:64px;top:22px;display:flex;align-items:center;gap:8px}
.brand-dot{width:26px;height:26px;border-radius:50%;border:3px solid var(--red)}
.brand-name{font-size:14px;font-weight:600;letter-spacing:2px;color:#3a3a3a;text-transform:uppercase}
.util-bar{left:370px;top:0;width:268px;height:22px;background:var(--blue);border-bottom:2px solid #0b3f66;display:flex;align-items:center;padding-left:12px;font-size:8px;color:var(--white)}
.util-bar .sep{margin:0 7px}
.util-phone{margin-left:auto;margin-right:10px;font-size:10.5px;display:flex;align-items:center;gap:5px}
.main-nav{top:44px;left:445px;display:flex;gap:21px;font-size:9px;color:var(--blue);letter-spacing:.2px}

/* hero */
.hero{left:0;top:70px;width:703px;height:316px;overflow:hidden}
.hero-photo{position:absolute;inset:0;background:radial-gradient(ellipse at 62% 35%,#8ea3b6 0%,#56677a 35%,#2a323d 75%,#1e242c 100%)}
.hero-wave{position:absolute;left:0;top:0}
.hero-welcome{left:69px;top:73px;color:var(--white)}
.hero-welcome .lead{font-size:21px;font-weight:300;line-height:1.1}
.hero-welcome .title{font-size:25px;font-weight:600;line-height:1.25;letter-spacing:-.3px}
.hero-about{left:66px;top:135px;width:235px;padding:3px 4px;background:rgba(20,24,30,.55);color:var(--white)}
.hero-about h2{font-size:9px;font-weight:700;color:var(--cyan);letter-spacing:.1px}
.hero-about p{font-size:9.2px;line-height:12px}
.hero-intro{left:77px;top:272px;width:560px;font-size:10px;line-height:15px;color:#eaf4fb}

/* services */
.section-title{font-size:15px;font-weight:600;color:var(--blue)}
.services-title{left:65px;top:420px}
.services-rule{left:64px;top:442px;width:574px;height:1px;background:var(--rule)}
.services-copy{left:67px;top:459px;width:172px;font-size:8.4px;line-height:14.3px;color:#555}
.service{width:80px;text-align:center;font-size:9px;line-height:12.5px;color:#555}
.service-ring{width:68px;height:68px;border-radius:50%;border:1.5px solid var(--blue);margin:0 auto 4px;display:flex;align-items:center;justify-content:center;background:var(--white)}
.service.active .service-ring{border:2px solid var(--red)}
.service-track{left:247px;top:566px}

/* difference */
.video{left:64px;top:603px;width:163px;height:90px;background:linear-gradient(120deg,#5b6670 0%,#a8b1b7 45%,#3f4a40 100%)}
.video-play{position:absolute;left:65px;top:34px;width:32px;height:22px;background:rgba(30,30,30,.8);border-radius:2px}
.difference-title{left:233px;top:602px;font-size:12.5px;color:#222}
.difference-copy{left:233px;top:625px;width:405px;font-size:7.7px;line-height:11.8px;color:#333}
.read-more{left:233px;top:681px;font-size:8px;color:var(--blue);text-decoration:underline}

/* panel */
.panel{left:0;top:728px;width:703px;height:231px;background:var(--panel);border-top:1px solid #e6e6e6;border-bottom:1px solid #e6e6e6}
.panel-title{font-family:"Montserrat",sans-serif;font-weight:400;font-size:12.5px;color:#222}
.news-item{width:175px;font-family:"Arimo",Arial,sans-serif;font-size:7.3px;line-height:11px;color:var(--soft)}
.news-item .head{white-space:nowrap}
.news-item .hl{color:var(--cyan)}
.news-item .date{color:var(--cyan);font-style:italic}
.news-item p{margin-top:6px;width:162px}
.news-rule{width:160px;height:1px;background:var(--rule)}
.view-all{font-size:9px;font-style:italic;color:#222}
.point{left:259px;width:157px;font-family:"Arimo",Arial,sans-serif;font-size:7.4px;line-height:10.5px;color:var(--soft);padding-bottom:10px;border-bottom:1px solid var(--rule)}
.quote{left:459px;top:777px;width:180px;height:88px;border:1px solid #c9c9c9;background:var(--white);padding:20px 10px 0 14px;font-family:"Arimo",Arial,sans-serif;font-size:7.6px;line-height:12px;color:#555}
.quote .mark{position:absolute;font-size:16px;color:#aaa;font-family:Georgia,serif}
.quote-tip{left:472px;top:864px}
.avatar{left:461px;top:874px;width:36px;height:36px;border-radius:50%;background:radial-gradient(circle at 50% 40%,#c9a37f,#5a3e2c)}
.person{left:502px;top:880px;font-family:"Arimo",Arial,sans-serif;font-size:8.5px;line-height:12px}
.person .name{color:var(--cyan)}
.person .role{color:#444}
.arrow{top:810px}

/* footer */
.footer{left:0;top:981px;width:703px;height:188px;background:var(--footer)}
.foot-col{top:1001px}
.foot-head{font-size:9.2px;font-weight:400;color:#ddd;display:flex;align-items:center;gap:10px}
.foot-head::after{content:"";width:38px;height:1px;background:#555}
.foot-links{list-style:none;margin-top:15px;font-size:7.6px;line-height:11.7px;color:var(--footer-text)}
.field{left:525px;width:113px;height:13px;background:#e7e7e7;border:1px solid #bbb;font-size:5.5px;color:#777;padding:3px 3px}
.send{left:525px;top:1138px;width:45px;height:14px;background:#1b8ed1;color:var(--white);font-size:8px;font-weight:700;text-align:center;line-height:14px;letter-spacing:.5px}
.foot-brand{left:76px;top:1129px;display:flex;align-items:center;gap:8px}
.foot-brand .brand-dot{border-color:#888;width:22px;height:22px}
.foot-brand .brand-name{color:#9a9a9a;font-size:11px}
.base{left:0;top:1169px;width:703px;height:31px;background:var(--footer-base);font-size:7.8px;color:var(--footer-text)}
.base-links{position:absolute;left:71px;top:11px}
.base-legal{position:absolute;right:74px;top:11px}
.base .sep{margin:0 10px}
</style>
</head>
<body>

<header>
  <div class="abs brand"><span class="brand-dot"></span><span class="brand-name">Veltrane Logistics</span></div>
  <div class="abs util-bar">
    <a href="#">Company</a><span class="sep">|</span><a href="#">Careers</a><span class="sep">|</span><a href="#">Contact Us</a>
    <span class="util-phone">
      <svg width="9" height="10" viewBox="0 0 10 10"><path d="M2 0.5 L3.6 0.5 L4.3 2.8 L3.2 3.7 Q4.3 6 6.3 6.9 L7.2 5.8 L9.5 6.5 L9.5 8.2 Q9 9.6 7.5 9.5 Q1 8.6 0.5 2.3 Q0.6 0.7 2 0.5Z" fill="#fff"/></svg>
      021-555-0148-20
    </span>
  </div>
  <nav class="abs main-nav"><a href="#">SOLUTIONS</a><a href="#">OUR PROCESS</a><a href="#">INDUSTRIES</a></nav>
</header>

<section class="abs hero">
  <div class="hero-photo" role="img" aria-label="Photo of a businessman holding a tablet with a glowing network of logistics icons over a world map"></div>
  <svg class="hero-wave" width="703" height="316" viewBox="0 0 703 316">
    <defs>
      <linearGradient id="band" x1="0" y1="0" x2="0" y2="1">
        <stop offset="0" stop-color="#2a86c8"/><stop offset="1" stop-color="#155f98"/>
      </linearGradient>
    </defs>
    <path d="M0 194 Q240 262 420 258 Q590 252 703 208 L703 316 L0 316Z" fill="url(#band)"/>
    <path d="M0 194 Q240 262 420 258 Q590 252 703 208" fill="none" stroke="#5fb4ea" stroke-width="2"/>
  </svg>
  <div class="abs hero-welcome">
    <div class="lead">Welcome To</div>
    <h1 class="title">Veltrane Logistics</h1>
  </div>
  <div class="abs hero-about">
    <h2>ABOUT SUPPLY CHAIN TRANSFORMATION</h2>
    <p>Lorem&nbsp; ipsum dolor sit amet consectetur adipiscing elit, sed do euismod tempor incidunt manga aliqua..</p>
  </div>
  <p class="abs hero-intro">Veltrane transforms supply chains by managing complexity, providing data-driven insights and implementing foeward-thinking innovation and actionable strategies that change business results..</p>
</section>

<section>
  <h2 class="abs section-title services-title">Our Services</h2>
  <div class="abs services-rule"></div>
  <p class="abs services-copy">Lorem ipsum dolor sit amet, consectetur adipisicing elit, sed do eiusmod tempor incidi-dunt ut labore et dolore magna aliqua. Ut enim ad minim veniam, quis nostrud exercita-tion ullamco laboris nisi ut aliquip ex ea com-modo consequat. Duis aute irure dolor in reprehenderit in voluptate velit esse cillum dolore eu fugiat nulla pariatur. Excepteur sint</p>

  <div class="abs service active" style="left:238px;top:476px">
    <div class="service-ring">
      <svg width="30" height="26" viewBox="0 0 30 26"><path d="M1 25 L1 10 L8 6 L8 10 L15 6 L15 10 L22 6 L22 10 L29 6 L29 25Z" fill="#d9141c"/><rect x="3" y="0" width="4" height="8" fill="#d9141c"/><g fill="#fff"><rect x="5" y="14" width="3" height="3"/><rect x="11" y="14" width="3" height="3"/><rect x="17" y="14" width="3" height="3"/><rect x="23" y="14" width="3" height="3"/><rect x="5" y="19" width="3" height="3"/><rect x="11" y="19" width="3" height="3"/><rect x="17" y="19" width="3" height="3"/><rect x="23" y="19" width="3" height="3"/></g></svg>
    </div>Factory Support</div>

  <div class="abs service" style="left:319px;top:462px">
    <div class="service-ring">
      <svg width="28" height="26" viewBox="0 0 28 26"><path d="M1 2 L5 2 L8 16 L24 16 L27 6 L7 6" fill="none" stroke="#1a7fc1" stroke-width="2.4"/><path d="M7.5 6 L26 6 L23.5 15 L9 15Z" fill="#1a7fc1"/><circle cx="10" cy="22" r="2.5" fill="#1a7fc1"/><circle cx="22" cy="22" r="2.5" fill="#1a7fc1"/></svg>
    </div>Retail Distributions</div>

  <div class="abs service" style="left:400px;top:452px">
    <div class="service-ring">
      <svg width="28" height="28" viewBox="0 0 28 28"><path d="M3 24 L16 11" stroke="#1a7fc1" stroke-width="4" stroke-linecap="round"/><path d="M15 12 A6 6 0 1 0 21 4 L18 7 L21 10 L24 7 A6 6 0 0 1 15 12Z" fill="#1a7fc1"/><path d="M5 5 L24 24" stroke="#1a7fc1" stroke-width="3.5" stroke-linecap="round"/><rect x="2" y="2" width="6" height="6" fill="#1a7fc1" transform="rotate(45 5 5)"/></svg>
    </div>Aftermarket<br>Support</div>

  <div class="abs service" style="left:481px;top:462px">
    <div class="service-ring">
      <svg width="32" height="28" viewBox="0 0 32 28"><g fill="#1a7fc1"><circle cx="11" cy="16" r="8"/><circle cx="24" cy="8" r="6"/><circle cx="24" cy="22" r="5"/></g><g fill="#1a7fc1" stroke="#1a7fc1" stroke-width="3" stroke-dasharray="2.5 2.5"><circle cx="11" cy="16" r="9.5" fill="none"/><circle cx="24" cy="8" r="7.3" fill="none"/><circle cx="24" cy="22" r="6.3" fill="none"/></g><g fill="#fff"><circle cx="11" cy="16" r="3"/><circle cx="24" cy="8" r="2.3"/><circle cx="24" cy="22" r="2"/></g></svg>
    </div>Critical Logistics</div>

  <div class="abs service" style="left:562px;top:476px">
    <div class="service-ring">
      <svg width="30" height="28" viewBox="0 0 30 28"><path d="M2 8 L10 8 Q10 4 13 4 Q16 4 16 8 L22 8 L22 14 Q26 14 26 17 Q26 20 22 20 L22 26 L2 26Z" fill="#1a7fc1"/><path d="M17 1 L28 3 L26 12 Q23 10 21 12 L19 4Z" fill="#5aa6d8"/></svg>
    </div>Supply Chain</div>

  <svg class="abs service-track" width="384" height="12" viewBox="0 0 384 12"><path d="M0 8 L184 8 L191 1 L198 8 L384 8" fill="none" stroke="#1a7fc1" stroke-width="1"/></svg>
</section>

<section>
  <div class="abs video" role="img" aria-label="Video still of two engineers working beside server racks">
    <span class="video-play"></span>
    <svg class="abs" style="left:77px;top:40px" width="8" height="10" viewBox="0 0 8 10"><path d="M0 0 L8 5 L0 10Z" fill="#fff"/></svg>
  </div>
  <h2 class="abs difference-title">The Veltrane Difference</h2>
  <p class="abs difference-copy">When you need our help, we will be there! No waiting for days for returned emails. No wondering if your request has been received. We make sure you know you're special to us and that your needs are important. It is a long established fact that a reader will be distracted by the readable content of a page when looking at its layout. The point of using Lorem Ipsum is that it has a more-or-less normal distribution of letters</p>
  <a class="abs read-more" href="#">READ MORE</a>
</section>

<section class="abs panel"></section>
<svg class="abs arrow" style="left:28px" width="14" height="36" viewBox="0 0 14 36"><path d="M12 1 L2 18 L12 35" fill="none" stroke="#cfcfcf" stroke-width="3"/></svg>
<svg class="abs arrow" style="left:662px" width="14" height="36" viewBox="0 0 14 36"><path d="M2 1 L12 18 L2 35" fill="none" stroke="#cfcfcf" stroke-width="3"/></svg>

<h2 class="abs panel-title" style="left:63px;top:746px">News and Events</h2>
<div class="abs news-item" style="left:64px;top:781px"><div class="head">Harlow Ridge Marlborough Sauvignon <span class="hl">Blanced etc</span></div><span class="date">posted on March 13, 2014 20:15</span>
  <p>Media release; summer has never tasted better than with Harlow Ridge's 2014 Sauvignon Blanc</p></div>
<div class="abs news-rule" style="left:64px;top:846px"></div>
<div class="abs news-item" style="left:64px;top:858px"><div class="head">Harlow Ridge Marlborough Sauvignon <span class="hl">Blanced etc</span></div><span class="date">posted on March 13, 2014 20:15</span>
  <p>Media release; summer has never tasted better than with Harlow Ridge's 2012 Sauvignon Blanc</p></div>
<a class="abs view-all" href="#" style="left:66px;top:921px">View All</a>

<h2 class="abs panel-title" style="left:264px;top:746px">A Different Perspective</h2>
<p class="abs point" style="top:779px">• We commit our own capital and resources to align with our clients' goals</p>
<p class="abs point" style="top:829px">• Unlike consultants, we implement and operate the solutions we design</p>
<p class="abs point" style="top:873px">• We guarantee business performance for our clients by investing in and executing the solutions we design.</p>

<h2 class="abs panel-title" style="left:458px;top:746px">Testimonials</h2>
<div class="abs quote">
  <span class="mark" style="left:6px;top:2px">&ldquo;</span>
  Lorem Ipsum is simply dummy text of the printing and typesetting industry. Lorem Ipsum has been the industry's standard dummy text ever since the 1500s, when
  <span class="mark" style="right:8px;bottom:-6px">&rdquo;</span>
</div>
<svg class="abs quote-tip" width="12" height="7" viewBox="0 0 12 7"><path d="M0 0 L12 0 L6 7Z" fill="#2fb1f0"/></svg>
<div class="abs avatar" role="img" aria-label="Portrait photo of the reviewer"></div>
<div class="abs person"><div class="name">Mirena Tolliver</div><div class="role">Manager</div></div>
<a class="abs view-all" href="#" style="left:461px;top:921px">View All</a>

<footer>
  <div class="abs footer"></div>
  <div class="abs foot-col" style="left:72px"><h3 class="foot-head">Our Process</h3>
    <ul class="foot-links"><li>Concept of operations</li><li>Supplying the infrastructure</li><li>Analyzing the data</li><li>Managing Complexity</li><li>Providing actionable stratrgies</li><li>nvesting in our clients sucess</li><li>Driving business results</li></ul></div>
  <div class="abs foot-col" style="left:227px"><h3 class="foot-head">Our Solutions</h3>
    <ul class="foot-links"><li>Business Analytics</li><li>Geigraphical Coverage</li><li>Project Financing</li><li>Project Implementation</li><li>Technology</li><li>Quality</li></ul></div>
  <div class="abs foot-col" style="left:367px"><h3 class="foot-head">Industries We Serve</h3>
    <ul class="foot-links"><li>Aerospace</li><li>Defense</li><li>Industrial</li><li>Manifacturing</li><li>Media &amp; Entertainment</li><li>Medical</li><li>Retail</li><li>Telecom &amp; Electronics</li></ul></div>
  <div class="abs foot-col" style="left:525px"><h3 class="foot-head">Company</h3></div>
  <div class="abs field" style="top:1030px">Name:</div>
  <div class="abs field" style="top:1046px">Last Name:</div>
  <div class="abs field" style="top:1063px">Email address:</div>
  <div class="abs field" style="top:1079px;height:56px">Message:</div>
  <div class="abs send">SEND</div>
  <div class="abs foot-brand"><span class="brand-dot"></span><span class="brand-name">Veltrane Logistics</span></div>
  <div class="abs base">
    <div class="base-links"><a href="#">Solutions</a><span class="sep">|</span><a href="#">Our Process</a><span class="sep">|</span><a href="#">Industries</a></div>
    <div class="base-legal">© VELTRANE, INC. 2014&nbsp;&nbsp; <a href="#">Privacy Policy</a><span class="sep" style="margin:0 6px">|</span><a href="#">Term of Use</a></div>
  </div>
</footer>

</body>
</html>
```